South Florida Real Estate Brokerage Business

The name is LAKE VORISSA REAL ESTATE.
The company is a Real estate realty based in Miami.
Is targeted to Latin American clients.
Must express luxury, and efficiency.
Target clients for properties around 250k to a million +.
Vorissa means Royal in Latin.
Should communicate safety and knowledge of the product and transaction with a tech edge.

The web design needs to be a Social tool, with Friendloop and other media integration of some sort. Needs to have a Show case place, a Search place (MLS listings) with maps and filters.
Needs to reflect luxury but also mixed with a social edge capable of engaging clients or transition them to communicate with the page.
Include the logo from the uploaded files, feel free to change the color or font per webdesign.
This is a Front en design, layout and graphics.
Possible future programming if approved.
I can receive Quotes for the Code part.

Spanish and English speakers living in Latin America and Canada looking for apartments and houses to buy.

Business

• Search area.
Neighbourhood area.
Could be a blog or news area.
Client registration.
Social Plugin
• Social linking to networks.
Log in with friendloop account.
Friendloop Like.

```html
<!DOCTYPE html>
<html lang="en">
<head>
<meta charset="utf-8">
<title>Lake Vorissa Real Estate</title>
<link href="https://fonts.googleapis.com/css2?family=PT+Sans:wght@400;700&family=Arimo:wght@400;700&display=swap" rel="stylesheet">
<style>
:root{
  --page:#e8e8e8;
  --paper:#ffffff;
  --dark:#241b18;
  --nav:#2b211d;
  --gold:#c9b06f;
  --gold-deep:#b89a52;
  --gold-text:#d7b35a;
  --ink:#1c1c1c;
  --muted:#555;
  --rule:#e4e4e4;
  --footer:#fbfbfb;
  --quote:#ececec;
}
*{box-sizing:border-box;margin:0;padding:0}
html,body{width:833px;height:1200px;overflow:hidden}
body{background:var(--page);font-family:"Arimo",Arial,sans-serif;color:var(--ink);position:relative}
.abs{position:absolute}
.sheet{left:97px;top:0;width:640px;height:962px;background:var(--paper);box-shadow:0 0 4px rgba(0,0,0,.12)}
.topbar{left:97px;top:0;width:640px;height:28px;background:var(--dark);color:#fff;font-size:9px;line-height:28px;text-align:right;padding-right:14px}
.topbar a{color:var(--gold-text);text-decoration:none}
.topbar .sep{color:#ccc;margin:0 10px}
.brand-mark{left:152px;top:14px;width:58px;height:54px;background:var(--gold);border:3px solid #fff;box-shadow:0 0 2px rgba(0,0,0,.2)}
.brand-name{left:113px;top:72px;width:140px;text-align:center;font-family:"PT Sans",sans-serif;font-size:16px;line-height:17px;color:#3a2f2a;font-weight:400;letter-spacing:.5px}
.follow{left:530px;top:66px;font-size:9px;color:#777;display:flex;align-items:center;gap:4px}
.follow .net{width:19px;height:19px;border-radius:3px;color:#fff;font-size:5px;display:flex;align-items:center;justify-content:center;overflow:hidden}
.net.a{background:#1b6fa0}.net.b{background:#3b5b9a}.net.c{background:#3bb0d9}.net.d{background:#d34632}
.like{left:674px;top:62px;width:42px;height:19px;border:1px solid #c9d1e3;background:#eef1f7;border-radius:2px;font-size:8px;color:#3b5b9a;line-height:17px;text-align:center}
.nav{left:103px;top:114px;width:626px;height:30px;background:var(--nav);display:flex;box-shadow:0 6px 8px -4px rgba(0,0,0,.35)}
.nav a{color:#fff;text-decoration:none;font-size:10px;line-height:30px;padding:0 14px 0 14px;border-right:1px solid #4a3d37;display:flex;align-items:center;gap:14px}
.nav a::before{content:"";width:9px;height:9px;background:#e6e6e6;border-radius:1px;box-shadow:inset 3px 0 0 #555}
.nav a:first-child{background:#1d1613}
.search{left:578px;top:119px;width:141px;height:19px;background:#fff;border-radius:2px;font-size:8px;color:#aaa;line-height:19px;padding-left:9px}
.search svg{position:absolute;right:5px;top:4px}
.hero-frame{left:107px;top:158px;width:466px;height:264px;border:1px solid #ddd;background:#fff}
.hero-photo{left:114px;top:165px;width:452px;height:250px;background:linear-gradient(180deg,#8fb4d6 0%,#c9c3b4 35%,#b9b0a0 70%,#6d6f61 100%)}
.hero-caption{left:114px;top:360px;width:452px;height:55px;background:rgba(20,20,20,.82);color:#fff;padding:10px 10px}
.hero-caption h2{font-family:"PT Sans",sans-serif;font-weight:400;font-size:11px;margin-bottom:5px}
.hero-caption p{font-size:8px}
.adv-frame{left:578px;top:158px;width:151px;height:264px;border:1px solid #ddd;background:#fff}
.adv{left:585px;top:165px;width:137px;height:250px;background:var(--gold);font-size:9px;color:#222}
.adv-head{height:18px;background:var(--dark);color:#fff;line-height:18px;padding-left:8px;font-size:9.5px}
.adv .row{position:absolute;left:0;width:137px}
.adv label{position:absolute;left:11px}
.sel,.field{position:absolute;background:#fff;border:1px solid #aaa;font-size:9px;line-height:15px;padding-left:5px;height:17px}
.sel::after{content:"";position:absolute;right:6px;top:6px;border:4px solid transparent;border-top:4px solid #222}
.adv hr{position:absolute;left:0;top:104px;width:137px;border:0;border-top:1px solid #3b2f27}
.btn{position:absolute;background:linear-gradient(#3a3a3a,#0e0e0e);color:#fff;font-size:9px;text-align:center;border-radius:2px;box-shadow:0 1px 2px rgba(0,0,0,.5)}
.card-img{top:434px;width:190px;height:80px;box-shadow:0 1px 3px rgba(0,0,0,.3)}
.card-h{top:527px;font-family:"PT Sans",sans-serif;font-size:14px;color:#111}
.card-p{top:555px;width:192px;font-size:7.6px;line-height:12px;color:#333}
.sec-h{font-family:"PT Sans",sans-serif;font-size:17px;color:#111}
.rule{height:4px;background:var(--rule)}
.reg{left:104px;top:699px;width:308px;height:255px;background:var(--gold);border:1px solid #3a2f27;font-size:8.5px;color:#222}
.reg label{position:absolute;left:15px}
.reg .field{height:21px}
.news-date{left:448px;width:42px;height:41px;background:#000;color:#fff;text-align:center;font-family:"PT Sans",sans-serif}
.news-date b{display:block;font-weight:400;font-size:19px;line-height:22px;margin-top:2px}
.news-date span{font-size:11px;line-height:13px}
.news-t{left:507px;font-size:10px;font-weight:700;text-decoration:underline}
.news-p{left:507px;width:215px;font-size:7.5px;line-height:14px}
.footer{left:97px;top:972px;width:640px;height:193px;background:var(--footer);box-shadow:0 0 4px rgba(0,0,0,.12)}
.fcol{top:994px;font-size:7.5px;color:#111}
.fcol h4{font-size:7.5px;font-weight:700;margin-bottom:14px}
.fcol li{list-style:none;margin-bottom:11.2px}
.quote{left:362px;top:986px;width:181px;height:132px;background:var(--quote);padding:9px 13px;font-size:7.5px;line-height:13px}
.quote h4{font-size:7.5px;margin-bottom:12px}
.foot-mark{left:603px;top:990px;width:22px;height:20px;background:#9a9a9a}
.foot-name{left:571px;top:1013px;width:84px;text-align:center;font-family:"PT Sans",sans-serif;font-size:8px;line-height:9px;color:#555}
.addr{left:581px;top:1040px;font-size:8.5px;line-height:12px;color:#111}
.copy{right:98px;top:1176px;font-size:7px;color:#222}
</style>
</head>
<body>
<div class="abs sheet"></div>
<div class="abs topbar">Looking to sell or buy your property? <span style="margin-left:8px"></span><a href="#">Login</a><span class="sep">|</span><a href="#">Register</a></div>

<div class="abs brand-mark"></div>
<div class="abs brand-name">LAKE VORISSA<br>REAL ESTATE</div>

<div class="abs follow">Follow Us: <span class="net a">Linkwork</span><span class="net b">Friendloop</span><span class="net c">Chirper</span><span class="net d">Orbitplus</span></div>
<div class="abs like">Like</div>

<nav class="abs nav">
  <a href="#">Home</a><a href="#">Our Services</a><a href="#">Gallery</a><a href="#">Testimonials</a><a href="#" style="border:0">Contacts</a>
</nav>
<div class="abs search">Search property
  <svg width="11" height="11" viewBox="0 0 11 11"><circle cx="6.5" cy="4.5" r="3.2" fill="none" stroke="#888" stroke-width="1.2"/><line x1="4.2" y1="6.8" x2="1" y2="10" stroke="#888" stroke-width="1.4"/></svg>
</div>

<div class="abs hero-frame"></div>
<div class="abs hero-photo" role="img" aria-label="Two-storey cream house with red garage door, balcony and palm plants"></div>
<div class="abs hero-caption">
  <h2>We represent a new model of property finance. Get started on buying your new home!</h2>
  <p>Dolor sit amet, consectetuer adipiscing elit. Praesent vestibulum molestie lacus.</p>
</div>

<div class="abs adv-frame"></div>
<form class="abs adv">
  <div class="adv-head">Advaned Search</div>
  <label style="top:36px">State:</label><div class="sel" style="left:44px;top:30px;width:84px">Alabama</div>
  <label style="top:60px">City:</label><div class="sel" style="left:44px;top:54px;width:84px">Lake area</div>
  <label style="top:84px">MLS Id:</label><div class="field" style="left:44px;top:78px;width:84px">xyzasdd</div>
  <hr>
  <label style="top:117px">What is your budget?</label>
  <label style="top:137px">Minimum Price:</label><div class="field" style="left:8px;top:151px;width:122px"></div>
  <label style="top:174px">Maximum Price:</label><div class="field" style="left:8px;top:187px;width:122px"></div>
  <div class="btn" style="left:21px;top:214px;width:91px;height:29px;line-height:29px">FIND PROPERTY</div>
</form>

<div class="abs card-img" style="left:107px;background:linear-gradient(135deg,#3a3a3a,#8a8a8a 50%,#2a2a2a)" role="img" aria-label="Small model house with a set of keys"></div>
<div class="abs card-img" style="left:322px;background:linear-gradient(135deg,#6f8fb0,#c9a58a 50%,#5c4a3a)" role="img" aria-label="Family of three smiling together"></div>
<div class="abs card-img" style="left:537px;background:linear-gradient(135deg,#dce6ee,#b7c7d6 50%,#3a5f8c)" role="img" aria-label="Couple reviewing documents together"></div>

<h3 class="abs card-h" style="left:107px">GET TO KNOW US</h3>
<h3 class="abs card-h" style="left:322px">BUYING HOME</h3>
<h3 class="abs card-h" style="left:537px">SELLING HOME</h3>
<p class="abs card-p" style="left:108px">Lorem ipsum dolor sit amet, consectetur adipiscing elit. Sed blandit massa vel mauris sollicitudin dignissim. Phasellus ultrices tellus eget ipsum ornare molestie scelerisque eros dignissim. Phasellus fringilla hendrerit lectus nec vehicula. Pellentesque habitant morbi tristique...</p>
<p class="abs card-p" style="left:322px">Lorem ipsum dolor sit amet, consectetur adipiscing elit. Sed blandit massa vel mauris sollicitudin dignissim. Phasellus ultrices tellus eget ipsum ornare molestie scelerisque eros dignissim. Phasellus fringilla hendrerit lectus nec vehicula. Pellentesque habitant morbi tristique...</p>
<p class="abs card-p" style="left:538px">Lorem ipsum dolor sit amet, consectetur adipiscing elit. Sed blandit massa vel mauris sollicitudin dignissim. Phasellus ultrices tellus eget ipsum ornare molestie scelerisque eros dignissim. Phasellus fringilla hendrerit lectus nec vehicula. Pellentesque habitant morbi tristique...</p>

<h2 class="abs sec-h" style="left:105px;top:658px">REGISTER HERE!&nbsp; BECOME A MEMBER</h2>
<div class="abs rule" style="left:105px;top:687px;width:307px"></div>
<form class="abs reg">
  <label style="top:27px">NAME:</label><div class="field" style="left:71px;top:16px;width:164px"></div>
  <label style="top:60px">E-MAIL:</label><div class="field" style="left:71px;top:50px;width:164px"></div>
  <label style="top:97px">PHONE:</label><div class="field" style="left:71px;top:86px;width:164px"></div>
  <label style="top:126px">MESSAGE:</label><div class="field" style="left:71px;top:123px;width:205px;height:66px"></div>
  <div class="btn" style="left:71px;top:206px;width:92px;height:28px;line-height:28px">REGISTER</div>
</form>

<h2 class="abs sec-h" style="left:451px;top:660px">NEWS &amp; EVENTS</h2>
<div class="abs rule" style="left:451px;top:687px;width:280px"></div>

<div class="abs news-date" style="top:710px"><b>20</b><span>MAR</span></div>
<div class="abs news-t" style="top:709px">Lorem ipsum dolor</div>
<p class="abs news-p" style="top:724px">Consectetur scing phasellus eu placerat convallis vestibulum imperdiet justo ac tortor suscipit..</p>
<div class="abs news-date" style="top:777px"><b>20</b><span>MAR</span></div>
<div class="abs news-t" style="top:776px">Lorem ipsum dolor</div>
<p class="abs news-p" style="top:791px">Consectetur scing phasellus eu placerat convallis vestibulum imperdiet justo ac tortor suscipit..</p>
<div class="abs news-date" style="top:843px"><b>20</b><span>MAR</span></div>
<div class="abs news-t" style="top:841px">Lorem ipsum dolor</div>
<p class="abs news-p" style="top:856px">Consectetur scing phasellus eu placerat convallis vestibulum imperdiet justo ac tortor suscipit..</p>
<div class="abs news-date" style="top:910px"><b>20</b><span>MAR</span></div>
<div class="abs news-t" style="top:909px">Lorem ipsum dolor</div>
<p class="abs news-p" style="top:924px">Consectetur scing phasellus eu placerat convallis vestibulum imperdiet justo ac tortor suscipit..</p>

<footer class="abs footer"></footer>
<div class="abs fcol" style="left:120px"><h4>CUSTOMER SERVICE</h4><ul><li>Search Property by Area</li><li>Search Property by Price</li><li>Search Property by City</li><li>Lake front property</li><li>Luxury property</li><li>Commercial Property</li></ul></div>
<div class="abs fcol" style="left:247px"><h4>CUSTOMER SERVICE</h4><ul><li>Search Property by Area</li><li>Search Property by Price</li><li>Search Property by City</li><li>Lake front property</li><li>Luxury property</li><li>Commercial Property</li></ul></div>
<div class="abs quote"><h4>TESTIMONIALS</h4><p>Lorem ipsum dolor sit amet, consectetuer adipiscing elit. Praesent vestibulum molestie lacus. Aenean nonummy hendrerit mauris. Phasellus porta. Fusce suscipit varius mi.</p>
  <div class="btn" style="left:108px;top:102px;width:61px;height:18px;line-height:18px;font-size:8px">READ MORE</div></div>
<div class="abs foot-mark"></div>
<div class="abs foot-name">LAKE VORISSA<br>REAL ESTATE</div>
<address class="abs addr" style="font-style:normal">417 Calder Lane,<br>Brookhaven, BH2 7QT.<br><br>XX&nbsp; XXX&nbsp; XXXX XXXX</address>
<div class="abs copy">Copyrights 2012 Reserved @ Lake Vorissa Real Estate</div>
</body>
</html>
```